Valdane Companies Business Card Design

We need a new business card for our Private Equity Real Estate Development firm, “Valdane” and our EB-5 regional center “Thornmere Regional Center” on one card. We prefer a design that is simple, elegant, and represents the luxury products we design and build as well as the financial security and stability our successful history has produced. We are an industry leader in our field and 3rd generation family business that has evolved into an institutional quality investment platform. Considered design size is standard business card dimensions (3.5 x 2 inches with an additional 1/8 inch space for design elements or backgrounds that extend beyond the finished size of your piece.

Target Market(s)

• High net worth individuals
• Highly skilled technical workers and physicians in the US seeking investment-based immigration opportunities
• Sophisticated private equity investors
• Intermediary partners include domestic attorneys and investment brokers, as well as international agent networks
• US real estate developers

Industry/Entity Type

Finance

Contact Information for Business Card

(Providing placeholder info for personal information, please design for longer character spaces, longer names and addresses etc..)
• Logo for Valdane
• Logo for Thornmere Regional Center
• Full name: Marcus Valdane
• Job title: CEO
• Email address: mvaldane@valdanecompanies.com
• Cell phone number: +1.555.314.2287
• Office number +1.555.628.4410
• Office address: Larkfield Court 5, 4817 Vista Orilla, San Ramon, CA.
• Website: www.valdanecompanies.com

Font styles to use
Serif
Sans Serif

Colors
ec1f27
ffffff
000000

Requirements
Must have
• • Logo for Valdane
• • Logo for Thornmere Regional Center
• - Use rounded corners
• (See .ai file included for logos)
Nice to have
• • Simple, elegant design
• • Aesthetically compatible with our website design (www.valdanecompanies.com)
• • Color palette including but not limited to white, black, and red (as per logos)
Should not have
• - Not too much red color
• - Do not stack both logos on top of each other

```html
<!DOCTYPE html>
<html lang="en">
<head>
<meta charset="utf-8">
<title>Valdane Companies Business Card</title>
<link rel="stylesheet" href="https://fonts.googleapis.com/css2?family=Roboto:wght@400;500&display=swap">
<style>
  :root {
    --backdrop: #2c2c2e;
    --card: #262527;
    --ink: #ffffff;
    --ink-soft: #e6e6e6;
    --accent: #a5182f;
  }
  * { box-sizing: border-box; margin: 0; padding: 0; }
  html, body { width: 1200px; height: 1200px; overflow: hidden; }
  body {
    background: var(--backdrop);
    font-family: "Roboto", Arial, sans-serif;
    position: relative;
  }
  .card {
    position: absolute;
    left: 194px;
    width: 880px;
    height: 502px;
    background: var(--card);
    border-radius: 32px;
  }
  .card--front { top: 34px; }
  .card--back { top: 664px; }

  .brand {
    position: absolute;
    left: 40px;
    top: 100px;
    display: flex;
    align-items: center;
    gap: 16px;
    color: var(--ink);
    font-weight: 500;
  }
  .brand__mark {
    width: 18px; height: 18px;
    background: var(--ink);
  }
  .brand__name {
    font-size: 44px;
    letter-spacing: 2px;
    text-transform: uppercase;
  }

  .person { position: absolute; left: 40px; top: 216px; color: var(--ink); }
  .person__name { font-size: 34px; font-weight: 500; line-height: 1; }
  .person__title { font-size: 22px; font-weight: 400; margin-top: 6px; color: var(--ink-soft); }

  .address {
    position: absolute; left: 40px; top: 296px;
    font-size: 20px; line-height: 22px; color: var(--ink-soft);
    font-style: normal;
  }

  .contacts { position: absolute; left: 40px; top: 360px; list-style: none; color: var(--ink-soft); font-size: 19px; }
  .contacts li { display: flex; align-items: center; height: 29px; }
  .contacts svg { width: 18px; height: 18px; margin-right: 25px; fill: none; stroke: var(--ink); stroke-width: 1.6; }

  .center-name {
    position: absolute;
    right: 44px;
    bottom: 40px;
    text-align: right;
    color: var(--accent);
    font-weight: 500;
    text-transform: uppercase;
  }
  .center-name__main { display: block; font-size: 54px; letter-spacing: 2px; line-height: 1; }
  .center-name__sub { display: block; font-size: 18px; letter-spacing: 9px; margin-top: 12px; }
</style>
</head>
<body>
  <section class="card card--front">
    <div class="brand">
      <span class="brand__mark"></span>
      <span class="brand__name">Valdane Capital</span>
    </div>

    <div class="person">
      <p class="person__name">Marcus Valdane</p>
      <p class="person__title">CEO</p>
    </div>

    <address class="address">
      Larkfield Court 5, 4817<br>
      Vista Orilla San Ramon, CA
    </address>

    <ul class="contacts">
      <li>
        <svg viewBox="0 0 18 18"><rect x="5" y="1" width="8" height="16" rx="1.5"/><line x1="8" y1="14" x2="10" y2="14"/></svg>
        +1555 - 314 - 2287
      </li>
      <li>
        <svg viewBox="0 0 18 18"><path d="M2 7c0-3 14-3 14 0v1h-3V6H5v2H2z"/><rect x="4" y="9" width="10" height="6" rx="1"/></svg>
        +1555 - 628 - 4410
      </li>
      <li>
        <svg viewBox="0 0 18 18"><rect x="1" y="4" width="16" height="11"/><polyline points="1,4 9,10 17,4"/></svg>
        mvaldane@valdanecompanies.com
      </li>
      <li>
        <svg viewBox="0 0 18 18"><circle cx="9" cy="9" r="7.5"/><ellipse cx="9" cy="9" rx="3.2" ry="7.5"/><line x1="1.5" y1="9" x2="16.5" y2="9"/></svg>
        www.valdanecompanies.com
      </li>
    </ul>
  </section>

  <section class="card card--back">
    <p class="center-name">
      <span class="center-name__main">Thornmere</span>
      <span class="center-name__sub">Regional Center</span>
    </p>
  </section>
</body>
</html>
```